Animal Eye Clinic needs a Business card

We are a new veterinary ophthalmology practice (Ridgeline Pet Vision Care) and we need a business card designed. We only see animal eyes - we are not a regular veterinary clinic. We already have a logo. We are looking for a professional, good looking business card to hand out to our clients. We are looking for something simple but professional and contemporary. Our logo is likely the only picture/graphic that needs to be on the card.
Updates

Contact Information for Business Card

Delia Vossman, BSc, DVM, MSc, DipACVO
Veterinary Ophthalmologist

Phone: 250.418.3927
Email: ridgelinepetvisioncare@mailbox-example.net
Website: ridgelinepetvisioncare-example.net
Address: 1874 Thornbury Rd
Kelowna, BC, V1X 4M9

Colors

Designer to choose colors to be used in the design.

Requirements
Must have
• Our logo (attached)

```html
<!DOCTYPE html>
<html lang="en">
<head>
<meta charset="utf-8">
<title>Ridgeline Pet Vision Care – Business Card</title>
<link rel="stylesheet" href="https://fonts.googleapis.com/css2?family=Roboto:wght@400;500;700&display=swap">
<style>
  :root {
    --stage: #1d1d1f;
    --card: #18181a;
    --card-edge: #232326;
    --gloss: #3a3a3e;
    --teal: #1497a6;
    --grey-text: #8d8d92;
    --light-text: #c9c9cd;
    --rule: #4a4a4f;
    --strip: #8a8a8e;
  }
  * { margin: 0; padding: 0; box-sizing: border-box; }
  html, body {
    width: 1200px; height: 800px; overflow: hidden;
    background: var(--stage);
    font-family: "Roboto", Arial, sans-serif;
  }
  .stage { position: relative; width: 1200px; height: 800px; }

  .card {
    position: absolute;
    width: 560px; height: 320px;
    background: var(--card);
    border: 1px solid var(--card-edge);
    border-radius: 16px;
    overflow: hidden;
    box-shadow: 0 18px 40px rgba(0,0,0,.55);
  }

  /* Front */
  .card-front { left: 90px; top: 60px; }
  .brand { display: flex; align-items: center; gap: 14px; }
  .brand-dot { width: 34px; height: 34px; border-radius: 50%; flex: none; }
  .brand-name {
    font-weight: 700; text-transform: uppercase;
    letter-spacing: 1px; line-height: 1.15;
  }
  .card-front .brand {
    position: absolute; left: 130px; top: 128px;
  }
  .card-front .brand-dot { background: var(--gloss); width: 42px; height: 42px; }
  .card-front .brand-name { color: var(--gloss); font-size: 26px; }

  /* Back */
  .card-back { left: 550px; top: 420px; }
  .card-back .brand { position: absolute; left: 36px; top: 40px; }
  .card-back .brand-dot { background: var(--teal); }
  .card-back .brand-name { color: var(--teal); font-size: 22px; }

  .top-rule {
    position: absolute; left: 300px; right: 36px; top: 44px;
    height: 1px; background: var(--rule);
  }
  .person { position: absolute; left: 36px; top: 140px; }
  .person-name { color: var(--teal); font-size: 17px; }
  .person-name strong { font-weight: 700; }
  .person-title { color: var(--grey-text); font-size: 13px; margin-top: 3px; }
  .mid-rule {
    position: absolute; left: 36px; width: 300px; top: 196px;
    height: 1px; background: var(--rule);
  }
  .contacts {
    position: absolute; left: 36px; top: 210px;
    list-style: none; color: var(--light-text); font-size: 12px;
  }
  .contacts li { display: flex; align-items: center; gap: 8px; margin-bottom: 7px; }
  .icon {
    width: 16px; height: 16px; border-radius: 50%;
    background: var(--teal); display: flex; align-items: center; justify-content: center;
  }
  .address {
    position: absolute; right: 36px; top: 200px; text-align: right;
    color: var(--light-text); font-size: 12px; line-height: 1.5;
  }
  .web-tab {
    position: absolute; right: 0; bottom: 16px;
    width: 260px; height: 30px; background: var(--teal);
    border-top-left-radius: 4px;
    color: #0d2a2e; font-size: 12px; font-weight: 500;
    display: flex; align-items: center; justify-content: center;
  }
  .base-strip {
    position: absolute; left: 0; right: 0; bottom: 0;
    height: 16px; background: var(--strip);
  }
</style>
</head>
<body>
<main class="stage">

  <section class="card card-front" aria-label="Card front">
    <div class="brand">
      <span class="brand-dot"></span>
      <span class="brand-name">Ridgeline<br>Pet Vision Care</span>
    </div>
  </section>

  <section class="card card-back" aria-label="Card back">
    <div class="brand">
      <span class="brand-dot"></span>
      <span class="brand-name">Ridgeline<br>Pet Vision Care</span>
    </div>
    <div class="top-rule"></div>

    <div class="person">
      <p class="person-name"><strong>Delia Vossman</strong>, BSc, DVM, MSc, DipACVO</p>
      <p class="person-title">Veterinary Ophthalmologist</p>
    </div>
    <div class="mid-rule"></div>

    <ul class="contacts">
      <li>
        <span class="icon">
          <svg width="9" height="9" viewBox="0 0 24 24"><path fill="#18181a" d="M6.6 10.8a15 15 0 0 0 6.6 6.6l2.2-2.2c.3-.3.7-.4 1-.2 1.1.4 2.3.6 3.6.6.6 0 1 .4 1 1V20c0 .6-.4 1-1 1A17 17 0 0 1 3 4c0-.6.4-1 1-1h3.5c.6 0 1 .4 1 1 0 1.3.2 2.5.6 3.6.1.3 0 .7-.2 1z"/></svg>
        </span>
        250.418.3927
      </li>
      <li>
        <span class="icon">
          <svg width="9" height="9" viewBox="0 0 24 24"><path fill="#18181a" d="M2 5h20v14H2zm2 2v.5l8 5 8-5V7l-8 5z"/></svg>
        </span>
        ridgelinepetvisioncare@mailbox-example.net
      </li>
    </ul>

    <address class="address" style="font-style:normal">
      1874 Thornbury Rd<br>Kelowna, BC, V1X 4M9
    </address>

    <div class="web-tab">ridgelinepetvisioncare-example.net</div>
    <div class="base-strip"></div>
  </section>

</main>
</body>
</html>
```